Wealth Education Business Needs Sharp Business Card Design

We need a business card design for a recently launched investor education business called Harbor Crest.

The final design should promote security, empowerment, self improvement and financial gain. The card will ideally promote the stature of the business.

For more information and colours please visit harborcrest.com.au

Target Market(s)

Corporate executives and high net worth individuals

Industry/Entity Type

Education

Contact Information for Business Card

```html
<!DOCTYPE html>
<html lang="en">
<head>
<meta charset="utf-8">
<title>Harbor Crest – Business Card</title>
<link rel="stylesheet" href="https://fonts.googleapis.com/css2?family=Lato:wght@400;700&display=swap">
<style>
  :root {
    --stage: #e9e7e4;
    --navy: #1f2a3d;
    --teal: #15999a;
    --ink: #3a3a3a;
    --wordmark-dark: #2f2f33;
    --gray-band: #5b5b5e;
    --paper: #ffffff;
  }
  * { margin: 0; padding: 0; box-sizing: border-box; }
  html, body {
    width: 1200px; height: 960px; overflow: hidden;
    background: var(--stage);
    font-family: "Lato", Arial, sans-serif;
  }
  .card {
    position: absolute; left: 270px; width: 645px; height: 369px;
    overflow: hidden;
    box-shadow: 0 4px 12px rgba(0,0,0,.25);
  }
  .card--front { top: 83px; background: var(--navy); }
  .card--back { top: 507px; background: var(--paper); }

  .wordmark {
    position: absolute; white-space: nowrap;
    font-weight: 400; text-transform: uppercase; letter-spacing: 5px;
  }
  .card--front .wordmark {
    left: 232px; top: 88px; font-size: 38px; color: var(--paper);
  }
  .card--back .wordmark {
    left: 42px; top: 162px; font-size: 25px; letter-spacing: 4px;
    color: var(--wordmark-dark);
  }

  .url-band {
    position: absolute; left: 0; top: 302px; width: 100%; height: 36px;
    background: var(--teal); color: var(--paper);
    font-size: 15px; line-height: 36px; padding-left: 45px;
  }

  .divider {
    position: absolute; left: 321px; top: 68px; width: 2px; height: 215px;
    background: linear-gradient(to bottom, transparent, var(--teal) 20%, var(--teal) 80%, transparent);
  }
  .details { position: absolute; left: 371px; top: 76px; color: var(--ink); font-size: 15px; line-height: 19px; }
  .details__name { color: var(--teal); font-weight: 700; font-size: 20px; line-height: 24px; }
  .details__address { margin-top: 21px; }
  .contact-list { list-style: none; margin-top: 20px; }
  .contact-list li { display: flex; align-items: center; gap: 10px; height: 20px; }
  .contact-list svg { width: 18px; height: 18px; fill: var(--teal); flex: none; }

  .swoosh { position: absolute; left: 0; bottom: 0; width: 645px; height: 369px; }
  .back-url {
    position: absolute; left: 0; bottom: 8px; width: 100%; text-align: center;
    color: var(--paper); font-size: 14px;
  }
</style>
</head>
<body>
  <section class="card card--front">
    <div class="wordmark">Harbor Crest</div>
    <div class="url-band">www.harborcrest.com.au</div>
  </section>

  <section class="card card--back">
    <div class="wordmark">Harbor Crest</div>
    <div class="divider"></div>
    <div class="details">
      <div class="details__name">Daniel Ashford</div>
      <div>Founder &amp; CEO</div>
      <div class="details__address">Level 4, 72 Marlow Street<br>Brightvale VIC 3100</div>
      <ul class="contact-list">
        <li><svg viewBox="0 0 18 18"><path d="M2 6c0-2 3-3 7-3s7 1 7 3v2h-4V6.5H6V8H2z M4 9h10l1 6H3z"/></svg>1300.415.726</li>
        <li><svg viewBox="0 0 18 18"><path d="M5 1h8a1 1 0 0 1 1 1v14a1 1 0 0 1-1 1H5a1 1 0 0 1-1-1V2a1 1 0 0 1 1-1zm1 2v10h6V3zm3 11.2a.9.9 0 1 0 0 1.8.9.9 0 0 0 0-1.8z"/></svg>0000.000.000</li>
        <li><svg viewBox="0 0 18 18"><path d="M1 4h16v11H1z M2.5 5.2 9 10l6.5-4.8v-.1H2.5z" fill-rule="evenodd"/></svg>support@harborcrest.com.au</li>
      </ul>
    </div>
    <svg class="swoosh" viewBox="0 0 645 369" aria-hidden="true">
      <path d="M0 362 Q322 296 645 362 Q322 314 0 362 Z" fill="var(--teal)"/>
      <path d="M0 369 L0 364 Q322 314 645 364 L645 369 Z" fill="var(--gray-band)"/>
    </svg>
    <div class="back-url">www.harborcrest.com.au</div>
  </section>
</body>
</html>
```